Business Card Design for Retail Product Line

We need a two-sided, full-color business card for a new oral care product line. The feel of the card should invoke emotions of happiness and health. It should be bright, cheerful and modern in appearance. The card should be mostly matte finish, but with elements of spot-gloss and/or raised/embossed features (print, logo, tag lines, etc.).

Target Market(s)

People who are into whole-body health, eat well and understand the importance of nutrition.

Industry/Entity Type

Health And Wellness

Contact Information for Business Card

The logo, color scheme and tag-lines have all been developed and artwork is attached. Card is to be standard-sized and should use a mix of clean, sans-serif fonts; the main font (DIN) is attached as well. The card will be used for 3 individuals and should include placeholders for:
1. Name
2. Title (for example, "CEO")
3. Business address
4. Phone number
5. Website
6. Email address

Font styles to use
Sans Serif
Other font styles liked:
• DIN font

Colors
faa54b
000000
5c5c5c
a2ce44

Requirements
Must have
• 2 sides
• Full color orange on one side
• Image of DNA leaves
• Tag line "shine from the roots up", on single side with orange background
• Company Logo (Plure) on same side as text (name, phone, address, etc.)
• Name, Title, Business Address, Phone Number, Website, Email address
• UPDATE: "Brisk Meadow", not "Brisk M Eadow"
Should not have
• Calligraphy
• Dark colors
• UPDATE!! Do not include "Turmeric infused toothpaste" on the business card
• UPDATE #2!! Do not include "Brisk Meadow" on the business card

```html
<!DOCTYPE html>
<html lang="en">
<head>
<meta charset="UTF-8">
<title>Plure Business Card</title>
<link href="https://fonts.googleapis.com/css2?family=Barlow:wght@400;600;700&family=Open+Sans:wght@400;700&display=swap" rel="stylesheet">
<style>
  :root {
    --orange: #faa54b;
    --orange-deep: #e8902f;
    --yellow: #f4c33a;
    --green: #a2ce44;
    --green-deep: #14923f;
    --ink: #000000;
    --grey: #5c5c5c;
    --paper: #ffffff;
    --backdrop: #ecebe8;
  }
  * { margin: 0; padding: 0; box-sizing: border-box; }
  html, body { width: 1200px; height: 900px; overflow: hidden; }
  body { background: var(--backdrop); position: relative; font-family: "Open Sans", sans-serif; }

  .card {
    position: absolute;
    width: 620px;
    height: 354px;
    overflow: hidden;
    box-shadow: 0 6px 18px rgba(0,0,0,0.18);
  }

  /* Front side */
  .card-front {
    left: 530px; top: 70px;
    background: linear-gradient(200deg, var(--yellow) 0%, var(--orange) 55%, var(--orange-deep) 100%);
  }
  .front-illustration {
    position: absolute; left: 0; top: 0; width: 180px; height: 230px;
    background: linear-gradient(160deg, rgba(162,206,68,0.85) 0%, rgba(244,195,58,0.6) 45%, rgba(250,165,75,0) 100%);
    border-bottom-right-radius: 120px;
  }
  .front-brand {
    position: absolute; left: 270px; top: 100px;
    font-family: "Barlow", sans-serif; font-weight: 600; font-size: 84px;
    color: var(--paper); letter-spacing: 1px;
  }
  .tagline {
    position: absolute; right: 40px; bottom: 36px; text-align: left;
    font-family: "Barlow", sans-serif; color: var(--paper); line-height: 0.95;
  }
  .tagline-lead { display: block; font-size: 44px; font-weight: 700; }
  .tagline-rest { display: block; font-size: 22px; font-weight: 700; letter-spacing: 0.5px; }

  /* Back side */
  .card-back { left: 60px; top: 470px; background: var(--paper); }
  .back-bands { position: absolute; inset: 0; }
  .holder { position: absolute; left: 62px; top: 26px; }
  .holder-name { font-family: "Open Sans", sans-serif; font-weight: 700; font-size: 19px; color: var(--green-deep); }
  .holder-title { font-size: 14px; color: var(--grey); }
  .back-illustration {
    position: absolute; left: 32px; top: 116px; width: 88px; height: 100px;
    background: linear-gradient(160deg, var(--green) 0%, #b8b8b8 70%);
    border-radius: 44px 44px 20px 20px;
  }
  .contact { position: absolute; left: 136px; top: 112px; font-size: 14px; color: var(--grey); line-height: 1.45; list-style: none; }
  .contact li { display: flex; align-items: center; gap: 8px; }
  .contact .address { padding-left: 20px; margin-bottom: 4px; }
  .contact svg { width: 12px; height: 12px; fill: var(--green-deep); flex: none; }
  .back-brand {
    position: absolute; left: 390px; top: 108px;
    font-family: "Barlow", sans-serif; font-weight: 600; font-size: 66px;
    color: var(--orange);
  }
</style>
</head>
<body>

<section class="card card-front">
  <div class="front-illustration" role="img" aria-label="DNA helix with green leaves"></div>
  <div class="front-brand">Plure</div>
  <p class="tagline">
    <span class="tagline-lead">shine</span>
    <span class="tagline-rest">FROM THE</span>
    <span class="tagline-rest">ROOTS UP</span>
  </p>
</section>

<section class="card card-back">
  <svg class="back-bands" width="620" height="354" viewBox="0 0 620 354" aria-hidden="true">
    <polygon points="22,24 44,24 30,50 22,50" fill="var(--orange)"/>
    <polygon points="44,24 52,24 38,50 30,50" fill="var(--green-deep)"/>
    <polygon points="0,256 292,256 270,284 0,284" fill="var(--green-deep)"/>
    <polygon points="300,284 620,284 620,354 268,354" fill="var(--orange)"/>
  </svg>

  <div class="holder">
    <p class="holder-name">Daniel Hartley</p>
    <p class="holder-title">Managing Director</p>
  </div>

  <div class="back-illustration" role="img" aria-label="DNA helix with green leaves"></div>

  <ul class="contact">
    <li class="address">12345, Address Goes Here<br>Country Name, 123456.</li>
    <li><svg viewBox="0 0 12 12"><path d="M2.5 1 4.5 1 5.5 3.6 4.3 4.6a7 7 0 0 0 3.1 3.1l1-1.2L11 7.5v2a1.5 1.5 0 0 1-1.5 1.5A8.5 8.5 0 0 1 1 2.5 1.5 1.5 0 0 1 2.5 1z"/></svg>021-555 0148</li>
    <li><svg viewBox="0 0 12 12"><path d="M1 3h10v6.5H1z M1 3l5 4 5-4" stroke="#fff" stroke-width="0.8"/></svg>info@plurecare.com</li>
    <li><svg viewBox="0 0 12 12"><circle cx="6" cy="6" r="5.5"/></svg>www.plurecare.com</li>
  </ul>

  <div class="back-brand">Plure</div>
</section>

</body>
</html>
```